I need a flyer made , the flyer can be one page or two pages or three pages . I will be posting this on Instagram and social media platforms. I am a luxury home builder , I am looking to hire a construction project manager . Below are some examples and ideas what can be on the flyer

We’re looking for a construction project manager who’s passionate about building luxury homes at the highest standards
We’re hiring construction project manager
* Experience 5+ years in residential project management with a strong portfolio of completed homes.
* location : Bergen County NJ
* excellent leadership skills, leads teams with confidence and clarity
* communicates seamlessly with architects , engineers, designers and clients
*knows how to manage budgets and timelines without compromising quality
*solves problems with a positive solution first mindset
* pays attention to every detail because in luxury the small things are the big things

Apply now , link in bio or DM to connect.

My logo is attached, my web site www.velstridebuilders.com
My style is modern but still warm and inviting. I like a clean classy look .

Please don’t add any images of chairs or people to the flyer , I do not want people on my flyer. Do not add standard images of offices and houses , we are luxury builders , we build homes over 2 million dollars. Keep a classy , simple modern look . High end .

You can add a white hard hat with my logo on it for a image , this is a suggestion does not have to be on my flyer ,

```html
<!DOCTYPE html>
<html lang="en">
<head>
<meta charset="utf-8">
<title>Velstride Builders — Hiring Construction Project Manager</title>
<link href="https://fonts.googleapis.com/css2?family=Josefin+Sans:wght@300;400;700&family=Source+Sans+3:wght@600&display=swap" rel="stylesheet">
<style>
  :root {
    --orange: #f7941d;
    --black: #0a0a0a;
    --ink: #1a1a1a;
    --white: #ffffff;
  }
  * { margin: 0; padding: 0; box-sizing: border-box; }
  html, body { width: 960px; height: 1200px; overflow: hidden; background: var(--white); }
  .flyer {
    position: relative; width: 960px; height: 1200px;
    background: var(--white); color: var(--ink);
    font-family: "Josefin Sans", sans-serif;
  }
  .hero { position: absolute; left: 0; top: 0; width: 960px; height: 510px; }
  .brand-band {
    position: absolute; left: 0; top: 350px; width: 403px; height: 158px;
    background: var(--black); color: var(--white);
    display: flex; flex-direction: column; justify-content: center; padding-left: 30px;
  }
  .brand-name {
    font-family: "Josefin Sans", sans-serif; font-weight: 300;
    font-size: 44px; letter-spacing: 3px; line-height: 1.05; text-transform: uppercase;
  }
  .accent-block {
    position: absolute; left: 0; top: 540px; width: 56px; height: 113px; background: var(--orange);
  }
  .intro {
    position: absolute; left: 94px; top: 540px;
    font-weight: 400; font-size: 25px; line-height: 41px; text-transform: uppercase;
    letter-spacing: 0.2px; color: var(--ink);
  }
  .rule { position: absolute; left: 95px; width: 695px; height: 2px; background: var(--orange); }
  .rule--top { top: 676px; }
  .rule--bottom { top: 731px; }
  .hiring-title {
    position: absolute; left: 94px; top: 691px;
    font-weight: 700; font-size: 23px; letter-spacing: 2.6px; color: var(--orange);
    text-transform: uppercase; white-space: nowrap;
  }
  .requirements {
    position: absolute; left: 104px; top: 760px; width: 760px; list-style: none;
    font-size: 15px; line-height: 31.7px; text-transform: uppercase; color: var(--ink);
  }
  .requirements li { position: relative; padding-left: 22px; }
  .requirements li::before {
    content: ""; position: absolute; left: 0; top: 12px;
    width: 9px; height: 9px; border-radius: 50%; background: var(--orange);
  }
  .requirements .wrap { display: block; margin-left: -19px; }
  .cta {
    position: absolute; right: 120px; top: 1080px; text-align: right;
  }
  .cta-line {
    font-family: "Source Sans 3", sans-serif; font-weight: 600;
    font-size: 26px; color: var(--orange);
  }
  .cta-web { font-size: 16px; margin-top: 6px; letter-spacing: 0.3px; color: var(--ink); }
  .corner-block {
    position: absolute; right: 0; top: 1087px; width: 75px; height: 48px; background: var(--black);
  }
</style>
</head>
<body>
<main class="flyer">
  <svg class="hero" viewBox="0 0 960 510" xmlns="http://www.w3.org/2000/svg">
    <defs>
      <linearGradient id="photo-tone" x1="0" y1="0" x2="1" y2="1">
        <stop offset="0" stop-color="#6f8a6e"/>
        <stop offset="0.35" stop-color="#e8ecf0"/>
        <stop offset="0.65" stop-color="#c9b39a"/>
        <stop offset="1" stop-color="#9ab8c8"/>
      </linearGradient>
    </defs>
    <polygon class="hero-frame" points="105,112 585,0 960,0 960,508 105,508" fill="#f7941d"/>
    <polygon class="hero-photo" role="img"
      aria-label="Modern luxury two-storey white villa at dusk with pool and architectural plans, a hand sketching with a pencil"
      points="125,130 588,20 610,42 960,24 960,500 125,500" fill="url(#photo-tone)"/>
    <g class="bars" fill="#0a0a0a">
      <rect x="412" y="350" width="34" height="158"/>
      <rect x="460" y="350" width="31" height="158"/>
      <rect x="503" y="350" width="29" height="158"/>
      <rect x="539" y="350" width="21" height="158"/>
      <rect x="566" y="350" width="14" height="158"/>
    </g>
    <rect x="403" y="500" width="557" height="8" fill="#f7941d"/>
  </svg>

  <div class="brand-band">
    <div class="brand-name">Velstride<br>Builders</div>
  </div>

  <div class="accent-block"></div>
  <p class="intro">
    We’re looking for a construction project manager<br>
    who’s passionate about building luxury homes<br>
    at the highest standards
  </p>

  <div class="rule rule--top"></div>
  <h1 class="hiring-title">We’re hiring construction project manager</h1>
  <div class="rule rule--bottom"></div>

  <ul class="requirements">
    <li>Experience 5+ years in residential project management with a strong <span class="wrap">portfolio of completed homes.</span></li>
    <li>Location : Bergen County NJ</li>
    <li>Excellent leadership skills, leads teams with confidence and clarity</li>
    <li>Communicates seamlessly with architects , engineers, designers and clients</li>
    <li>Knows how to manage budgets and timelines without compromising quality</li>
    <li>Solves problems with a positive solution first mindset</li>
    <li>Pays attention to every detail because in luxury the small things are <span class="wrap">the big things</span></li>
  </ul>

  <div class="cta">
    <p class="cta-line">Apply now , link in bio or DM to connect.</p>
    <p class="cta-web">WWW.VELSTRIDEBUILDERS.COM</p>
  </div>
  <div class="corner-block"></div>
</main>
</body>
</html>
```